Redesign and move to Wordpress for corvandel.com

Our website needs a redesign and at the same time we are moving it to Wordpress. Please help us with a new digital professional look and feel.

We are an Australian Software Engineering company specialising in advanced software development using in A.I., PLatform Engineering, Integration and Cloud. See the current corvandel.com for more information about us.

```html
<!DOCTYPE html>
<html lang="en">
<head>
<meta charset="utf-8">
<title>Corvandel — Software & Tech Development</title>
<link rel="stylesheet" href="https://fonts.googleapis.com/css2?family=Lexend:wght@300;400;500&family=Roboto:ital,wght@0,400;0,500;0,700;1,700&display=swap">
<style>
:root{
  --ink:#111318;
  --text:#555a63;
  --muted:#7b8089;
  --blue:#1f5fd6;
  --blue-deep:#0b3a86;
  --blue-bright:#2f7be8;
  --violet:#8f64e8;
  --lav:#c9c2f2;
  --section-tint:#f0f4fc;
  --footer-tint:#f4f5f8;
  --line:#e3e6ec;
  --white:#fff;
}
*{margin:0;padding:0;box-sizing:border-box}
html,body{width:1200px;height:4210px;overflow:hidden;background:var(--white)}
body{position:relative;font-family:"Roboto",Arial,sans-serif;color:var(--ink)}
.abs{position:absolute}
.display{font-family:"Lexend",Arial,sans-serif}

/* nav */
.nav{left:0;top:0;width:1200px;height:76px;border-bottom:1px solid var(--line);background:var(--white);z-index:5}
.brand{left:28px;top:20px;font-family:"Lexend",sans-serif;font-size:30px;font-weight:300;letter-spacing:1px;display:flex;align-items:center;gap:12px}
.brand i{width:26px;height:26px;border:2.5px solid var(--ink);display:block}
.menu{right:100px;top:26px;display:flex;gap:33px;font-size:16px}
.search{right:30px;top:24px}

/* hero */
.hero{left:0;top:77px;width:1200px;height:560px;background:linear-gradient(100deg,#eaf1fd 0%,#fff 28%,#fff 60%,#f1ecfa 100%)}
.eyebrow{font-size:11px;letter-spacing:3px;color:var(--muted);text-transform:uppercase}
.hero-title{left:75px;top:138px;font-size:52px;font-weight:400;line-height:66px;color:var(--ink);z-index:3;white-space:nowrap}
.btn-grad{left:75px;top:400px;width:170px;height:48px;background:linear-gradient(90deg,var(--blue-bright),var(--violet));color:#fff;font-size:13px;letter-spacing:3px;display:flex;align-items:center;justify-content:center;z-index:3}
.hero-art{left:520px;top:65px;width:290px;height:400px;transform:skewY(6deg);background:linear-gradient(135deg,#fafafd,#e7e6f2);box-shadow:20px 30px 40px rgba(80,70,120,.18);z-index:1}

/* intro */
.intro-title{left:0;top:710px;width:1200px;text-align:center;font-size:36px;font-weight:500}
.intro-text{left:180px;top:770px;width:840px;text-align:center;font-size:15px;line-height:24px;color:var(--text)}

/* features */
.feature{top:1100px;width:310px}
.feature .num{font-family:"Lexend",sans-serif;font-size:110px;line-height:100px;font-weight:400;background:linear-gradient(90deg,var(--lav),#a7c4f3);-webkit-background-clip:text;background-clip:text;color:transparent;opacity:.85}
.feature h3{position:absolute;top:38px;left:0;font-family:"Lexend",sans-serif;font-size:29px;line-height:38px;font-weight:400;color:var(--ink)}
.feature p{margin-top:32px;font-size:14px;line-height:22px;color:var(--text);text-align:justify}
.feature .more{margin-top:38px;display:flex;align-items:center;gap:16px;font-size:13px}
.feature .more:before{content:"";width:72px;height:1px;background:var(--blue-bright)}

/* why */
.why{left:0;top:1482px;width:1200px;height:765px;background:var(--section-tint)}
.why-label{left:61px;top:168px;font-size:18px;display:flex;align-items:center;gap:12px}
.why-label:before{content:"";width:45px;height:2px;background:var(--ink)}
.why-title{left:61px;top:215px;font-size:32px;font-weight:500;color:var(--blue-deep)}
.why-text{left:61px;top:272px;width:385px;font-size:14px;line-height:21px;color:var(--text)}
.why-text p+p{margin-top:16px}
.card{width:290px;text-align:center;display:flex;flex-direction:column;align-items:center;justify-content:center;gap:8px;padding:0 40px}
.card h4{font-size:19px;font-weight:500;margin-top:6px}
.card p{font-size:14px;line-height:21px}
.card.solid{background:linear-gradient(135deg,var(--blue),var(--blue-deep));color:#fff}
.card.plain{background:#fff;color:var(--ink)}
.card.plain p{color:var(--text)}

/* partners */
.partners-label{left:108px;top:2350px}
.partners-title{left:108px;top:2378px;font-size:37px;line-height:43px;font-weight:400}
.partners-text{left:108px;top:2528px;width:340px;font-size:14px;line-height:22px;color:var(--text)}
.btn-line{left:108px;top:2653px;width:170px;height:50px;border:1.5px solid var(--ink);font-size:13px;letter-spacing:3px;display:flex;align-items:center;justify-content:center}
.mark{font-family:"Roboto",sans-serif;font-weight:700;font-size:36px;color:var(--ink);display:flex;align-items:center;gap:10px}
.mark b{width:30px;height:30px;background:var(--ink);display:block}
.mark.big{font-size:40px}

/* services */
.svc-label{left:0;top:3095px;width:1200px;text-align:center;color:var(--blue);font-size:22px;font-weight:500;letter-spacing:2px}
.svc-title{left:0;top:3133px;width:1200px;text-align:center;font-family:"Lexend",sans-serif;font-size:34px;font-weight:400}
.svc-rule{left:573px;top:3190px;width:54px;height:2px;background:var(--blue)}
.svc{top:3238px;width:323px;height:485px;box-shadow:0 2px 12px rgba(0,0,0,.12);text-align:center;padding:50px 30px 0}
.svc.plain{background:#fff}
.svc.solid{background:linear-gradient(160deg,var(--blue-bright),var(--blue-deep) 20%,var(--blue-bright) 60%,#4a90ec);color:#fff}
.svc svg{display:block;margin:0 auto 30px}
.svc h4{font-size:19px;font-weight:500;line-height:23px}
.svc p{margin-top:16px;font-size:13px;line-height:24px;color:var(--muted)}
.svc.solid p{color:#fff}
.go{top:3700px;width:46px;height:46px;border-radius:50%;background:#fff;box-shadow:0 2px 8px rgba(0,0,0,.15);display:flex;align-items:center;justify-content:center;color:var(--blue)}
.dots{left:575px;top:3768px;display:flex;gap:12px}
.dots i{width:8px;height:8px;border-radius:50%;background:#cdd7ea;display:block}
.dots i:first-child{background:var(--blue-bright)}

/* footer band */
.band{left:0;top:3895px;width:1200px;height:315px;background:var(--footer-tint)}
.band-title{left:38px;top:50px;font-family:"Lexend",sans-serif;font-size:38px;font-weight:400;line-height:54px;letter-spacing:1px}
.band-sub{left:38px;top:170px;font-size:37px;font-weight:700;font-style:italic;color:var(--blue)}
.news-title{left:731px;top:55px;font-family:"Lexend",sans-serif;font-size:29px;font-weight:300}
.news-text{left:731px;top:100px;font-size:15px;color:var(--muted)}
.news-input{left:731px;top:155px;width:266px;height:43px;background:#fff;border:1px solid var(--line);font-size:14px;color:var(--muted);padding:12px 14px}
.news-btn{left:997px;top:155px;width:115px;height:43px;background:#111;color:#fff;font-size:15px;display:flex;align-items:center;justify-content:center;border-radius:2px}
</style>
</head>
<body>

<header class="abs nav">
  <div class="abs brand"><i></i>corvandel</div>
  <nav class="abs menu"><span>Services</span><span>Contact</span><span>About</span><span>Blog</span></nav>
  <svg class="abs search" width="22" height="22" viewBox="0 0 22 22"><circle cx="9" cy="9" r="6" fill="none" stroke="#111" stroke-width="2.5"/><line x1="13.5" y1="13.5" x2="19" y2="19" stroke="#111" stroke-width="3"/></svg>
</header>

<section class="abs hero">
  <div class="abs hero-art" role="img" aria-label="Illustration of a standing hardcover book with a pale geometric cover"></div>
  <div class="abs eyebrow" style="left:75px;top:104px;z-index:3">Modern Technologies</div>
  <h1 class="abs display hero-title">Software &amp; Tech<br>Development for<br>the Future</h1>
  <div class="abs btn-grad">APPLY NOW</div>
</section>

<h2 class="abs intro-title">Tomorrow, delivered today</h2>
<p class="abs intro-text">At Corvandel, we craft bespoke software solutions that are not available on the market. By building organizations market-leading products, process automation, legacy system enablement, or advanced intelligent systems, we empower our customers to achieve a competitive edge in their industry.</p>

<article class="abs feature" style="left:37px">
  <div class="num">01</div><h3>Manage your<br>data efficiently</h3>
  <p>Lorem ipsum dolor sit amet ridiculus consectetuer adipiscing elit. Aenean commodo ligula eget dolor. Montes est massa. Cum sociis Theme natoq</p>
  <div class="more">VIEW MORE</div>
</article>
<article class="abs feature" style="left:412px">
  <div class="num">02</div><h3>Built with neat<br>utility features</h3>
  <p>Lorem ipsum dolor sit amet ridiculus consectetuer adipiscing elit. Aenean commodo ligula eget dolor. Montes est massa. Cum sociis Theme natoq</p>
  <div class="more">VIEW MORE</div>
</article>
<article class="abs feature" style="left:787px">
  <div class="num">03</div><h3>Built with neat<br>utility features</h3>
  <p>Lorem ipsum dolor sit amet ridiculus consectetuer adipiscing elit. Aenean commodo ligula eget dolor. Montes est massa. Cum sociis Theme natoq</p>
  <div class="more">VIEW MORE</div>
</article>

<section class="abs why">
  <div class="abs why-label">WHY CHOOSE US</div>
  <h2 class="abs why-title">What Problems Do We Solve</h2>
  <div class="abs why-text">
    <p>we help businesses overcome their toughest challenges with custom software solutions.</p>
    <p>Our solutions grow with your business, ensuring seamless performance at every stage.We modernize legacy software and integrate cutting-edge technologies to keep you competitive. We build user-friendly, engaging apps and platforms that enhance customer experience.We implement robust security measures to protect your business and customer data.</p>
  </div>

  <div class="abs card solid" style="left:512px;top:169px;height:225px">
    <svg width="52" height="52" viewBox="0 0 52 52" fill="none" stroke="#fff" stroke-width="2"><rect x="12" y="12" width="28" height="28" rx="3"/><text x="26" y="31" fill="#fff" stroke="none" font-size="12" text-anchor="middle" font-family="Roboto">AI</text><path d="M18 4v8M26 4v8M34 4v8M18 40v8M26 40v8M34 40v8M4 18h8M4 26h8M4 34h8M40 18h8M40 26h8M40 34h8"/></svg>
    <h4>Custom Development</h4><p>Astonished set expression solicitude way admiration</p>
  </div>
  <div class="abs card plain" style="left:831px;top:121px;height:230px">
    <svg width="52" height="52" viewBox="0 0 52 52" fill="none" stroke="#1f5fd6" stroke-width="2"><rect x="6" y="30" width="40" height="14" rx="2"/><circle cx="26" cy="18" r="8"/><circle cx="26" cy="18" r="3"/><path d="M26 6v4M26 26v4M14 18h4M34 18h4"/></svg>
    <h4>Systems Integration</h4><p>Astonished set expression solicitude way admiration</p>
  </div>
  <div class="abs card plain" style="left:512px;top:413px;height:230px">
    <svg width="56" height="56" viewBox="0 0 56 56" fill="none" stroke="#1f5fd6" stroke-width="2"><path d="M16 34a10 10 0 0 1 2-20 13 13 0 0 1 24 4 8 8 0 0 1-2 16z"/><path d="M22 34v12M28 34v16M34 34v12"/><circle cx="22" cy="48" r="2"/><circle cx="34" cy="48" r="2"/></svg>
    <h4>Cloud Computing</h4><p>Astonished set expression solicitude way admiration</p>
  </div>
  <div class="abs card solid" style="left:831px;top:370px;height:228px">
    <svg width="52" height="52" viewBox="0 0 52 52" fill="none" stroke="#fff" stroke-width="2"><path d="M14 30a9 9 0 0 1 2-18 12 12 0 0 1 22 4 7 7 0 0 1-2 14z"/><circle cx="30" cy="32" r="8"/><path d="M36 38l8 8"/></svg>
    <h4>Data Analytics</h4><p>Astonished set expression solicitude way admiration</p>
  </div>
</section>

<div class="abs eyebrow partners-label">Partners</div>
<h2 class="abs display partners-title">Trusted and<br>Supported by<br>Many</h2>
<p class="abs partners-text">our clients aren't just customers—they're partners in innovation. Leading businesses across industries trust us to deliver reliable, scalable, and future-ready solutions.</p>
<div class="abs btn-line">APPLY NOW</div>

<div class="abs mark" style="left:660px;top:2378px;height:50px"><b></b>Northvale</div>
<div class="abs mark" style="left:945px;top:2378px;height:50px">Quillo</div>
<div class="abs mark" style="left:660px;top:2514px;height:50px">Cadenza</div>
<div class="abs mark" style="left:925px;top:2514px;height:50px"><b style="border-radius:50%"></b>Forkhaus</div>

<div class="abs mark" style="left:15px;top:2880px;height:60px;font-size:32px"><b></b>St Aldric's</div>
<div class="abs mark big" style="left:330px;top:2880px;height:60px">Kestrel</div>
<div class="abs mark" style="left:635px;top:2880px;height:60px"><b style="border-radius:50%"></b>Solvana</div>
<div class="abs mark" style="left:970px;top:2880px;height:60px;font-size:24px"><b></b>Harbourline</div>

<div class="abs svc-label">SERVICES</div>
<h2 class="abs svc-title">What we do</h2>
<div class="abs svc-rule"></div>

<article class="abs svc plain" style="left:77px">
  <svg width="90" height="80" viewBox="0 0 90 80" fill="none" stroke="#1f5fd6" stroke-width="2"><rect x="15" y="30" width="60" height="34" rx="2"/><path d="M35 70h20M45 64v6"/><circle cx="45" cy="28" r="12"/><circle cx="45" cy="28" r="4"/><path d="M45 10v6M45 40v6M27 28h6M57 28h6"/></svg>
  <h4>ENTERPRISE Systems<br>Integration</h4>
  <p>Automate your business processes internally or externally to improve data quality and process efficiency</p>
</article>
<article class="abs svc solid" style="left:438px">
  <svg width="90" height="80" viewBox="0 0 90 80" fill="none" stroke="#8fc0ff" stroke-width="2"><circle cx="45" cy="40" r="10"/><circle cx="45" cy="40" r="4"/><path d="M45 10v20M45 50v20M15 40h20M55 40h20M24 19l14 14M52 47l14 14M66 19L52 33M38 47L24 61"/><circle cx="45" cy="8" r="3"/><circle cx="45" cy="72" r="3"/><circle cx="13" cy="40" r="3"/><circle cx="77" cy="40" r="3"/></svg>
  <h4>Microservices</h4>
  <p>Leverage Microservices Architecture to enable quick deployment, dynamically scalable service performance, team productivity and more</p>
</article>
<article class="abs svc plain" style="left:798px">
  <svg width="90" height="80" viewBox="0 0 90 80" fill="none" stroke="#1f5fd6" stroke-width="2"><path d="M25 46a14 14 0 0 1 3-28 18 18 0 0 1 34 6 11 11 0 0 1-3 22z"/><rect x="33" y="24" width="24" height="16" rx="2"/><path d="M33 30h24M33 35h24M30 46v14M45 46v22M60 46v14"/><circle cx="30" cy="62" r="3"/><circle cx="45" cy="70" r="3"/><circle cx="60" cy="62" r="3"/></svg>
  <h4>Plateform Engineering</h4>
  <p>For organisations looking to manage the security and cost risks around their cloud infrastructure management for applications</p>
</article>
<div class="abs go" style="left:216px"><svg width="12" height="14" viewBox="0 0 12 14"><path d="M3 2l6 5-6 5" fill="none" stroke="currentColor" stroke-width="2"/></svg></div>
<div class="abs go" style="left:576px"><svg width="12" height="14" viewBox="0 0 12 14"><path d="M3 2l6 5-6 5" fill="none" stroke="currentColor" stroke-width="2"/></svg></div>
<div class="abs go" style="left:936px"><svg width="12" height="14" viewBox="0 0 12 14"><path d="M3 2l6 5-6 5" fill="none" stroke="currentColor" stroke-width="2"/></svg></div>
<div class="abs dots"><i></i><i></i><i></i></div>

<section class="abs band">
  <h2 class="abs band-title">AUSTRALIA'S LARGEST HEALTH<br>CHARITY IMPLEMENTS</h2>
  <div class="abs band-sub">CORVANDEL API MSG BUS</div>
  <h3 class="abs news-title">Join Our Newsletter</h3>
  <p class="abs news-text">Register to our newsletter to find out more.</p>
  <div class="abs news-input">Enter your Email Adress</div>
  <div class="abs news-btn">Subscribe</div>
</section>

</body>
</html>
```